Improved Business Card, Government Contracting

We are looking to update the design of our business cards. We would like to create a template that can be used for future employees and easy to update.

Halvorsen Advisory Partners, LLC is a Service Disabled Veteran Owned Small Business with headquarters located in Ashcombe, MO. Our current website is www.hvadpt.com. We have contracts in KS and VA with expansion opportunities in various other states. Our primary line of work is within government contracting and providing consulting services to various organizations within the Bureau of Civic Readiness. We would like to project a professional image of our company that is consistent with the industry. Provided are previous versions of our business card template that shows our logo as well. We would like to make sure the information on the cards are easily noticeable .

Target Market(s)

Government Officials
Fellow Small Business Contractors
Large Business Contractors (ex. TQLB, Pellwick Darrow, Fenwey Marsh Colquitt)

Industry/Entity Type

Business

Contact Information for Business Card

Dale Forsyth
Office Manager
Halvorsen Advisory Partners
Ph: 555.204.7716
Email: d.forsyth@hvadpt.us
www.hvadpt.com

Requirements
Must have
• The business mailing address is:
• 48730 212th Crescent
• Ashcombe, MO 66091
Nice to have
• Embossed lettering

```html
<!DOCTYPE html>
<html lang="en">
<head>
<meta charset="utf-8">
<title>Halvorsen Advisory Partners – Business Card</title>
<link rel="stylesheet" href="https://fonts.googleapis.com/css2?family=Lato:wght@400;700;900&display=swap">
<style>
  :root {
    --brand-blue: #2e3192;
    --accent-blue: #3d5aa8;
    --brand-yellow: #f7ea1f;
    --ink: #1d1d1f;
    --paper: #ffffff;
    --backdrop: #e4e2df;
  }
  * { box-sizing: border-box; margin: 0; padding: 0; }
  html, body {
    width: 1200px; height: 1000px; overflow: hidden;
    background: var(--backdrop);
    font-family: "Lato", Arial, sans-serif;
  }
  .stage { position: relative; width: 1200px; height: 1000px; }

  .card {
    position: absolute;
    width: 580px; height: 332px;
    box-shadow: 0 6px 18px rgba(0,0,0,.18);
  }

  /* Front side */
  .card-front {
    left: 150px; top: 110px;
    background: var(--brand-blue);
    display: flex; align-items: center; justify-content: center;
  }
  .front-name {
    color: var(--brand-yellow);
    font-weight: 900;
    font-size: 40px;
    line-height: 1.15;
    text-align: center;
    letter-spacing: .3px;
  }

  /* Back side */
  .card-back {
    left: 470px; top: 560px;
    background: var(--paper);
  }
  .back-name {
    position: absolute; left: 30px; top: 138px; width: 270px;
    color: var(--accent-blue);
    font-weight: 700; font-size: 24px; line-height: 1.15;
    text-align: center;
  }
  .divider {
    position: absolute; left: 318px; top: 60px;
    width: 2px; height: 216px;
    background: linear-gradient(to bottom, var(--accent-blue), rgba(61,90,168,.35));
  }
  .contact {
    position: absolute; left: 342px; top: 52px; width: 230px;
    color: var(--ink);
  }
  .person-name { color: var(--accent-blue); font-weight: 900; font-size: 21px; line-height: 1.1; }
  .person-title { font-weight: 700; font-size: 16px; margin-bottom: 16px; }
  .contact-list { list-style: none; }
  .contact-list li {
    display: flex; align-items: center; gap: 8px;
    font-weight: 700; font-size: 16.5px; line-height: 1.45;
  }
  .contact-list svg { width: 14px; height: 14px; flex: none; fill: var(--accent-blue); }
  .address { margin-top: 22px; font-weight: 700; font-size: 18px; line-height: 1.3; }
</style>
</head>
<body>
<main class="stage">
  <section class="card card-front" aria-label="Business card front">
    <p class="front-name">Halvorsen Advisory<br>Partners</p>
  </section>

  <section class="card card-back" aria-label="Business card back">
    <p class="back-name">Halvorsen Advisory Partners</p>
    <div class="divider"></div>
    <div class="contact">
      <p class="person-name">Dale Forsyth</p>
      <p class="person-title">Office Manager</p>
      <ul class="contact-list">
        <li>
          <svg viewBox="0 0 16 16" aria-hidden="true"><path d="M1 5c0-2 3-3 7-3s7 1 7 3v1h-3V4.5C11 4 9.5 3.8 8 3.8S5 4 4 4.5V6H1zM3 8l2-2h6l2 2v6H3zm5 1.2a2 2 0 100 4 2 2 0 000-4z"/></svg>
          555.204.7716
        </li>
        <li>
          <svg viewBox="0 0 16 16" aria-hidden="true"><path d="M1 3h14v10H1zm1.5 1.2V12h11V4.2L8 8.6z"/></svg>
          d.forsyth@hvadpt.us
        </li>
        <li>
          <svg viewBox="0 0 16 16" aria-hidden="true"><path d="M8 1a7 7 0 100 14A7 7 0 008 1zm0 1.5c.8 0 1.7 1.5 2 3.8H6c.3-2.3 1.2-3.8 2-3.8zM2.6 7.2h2.3a13 13 0 000 1.6H2.6a5.5 5.5 0 010-1.6zm3.3 0h4.2a12 12 0 010 1.6H5.9a12 12 0 010-1.6zm5.2 0h2.3a5.5 5.5 0 010 1.6h-2.3a13 13 0 000-1.6zM6 9.7h4c-.3 2.3-1.2 3.8-2 3.8s-1.7-1.5-2-3.8z"/></svg>
          www.hvadpt.com
        </li>
      </ul>
      <p class="address">48730 212th Crescent<br>Ashcombe, MO 66091</p>
    </div>
  </section>
</main>
</body>
</html>
```